Life Coaching business needs a new flyer

We are an Australian business that specialises in Life Coaching, Career Coaching, Health and Wellness Coaching, Yoga and Pilates. We need a A4 double sided flyer that is full colour and folded to DL format. I have attached a couple of designs that I like and some pictures and would like the flyer to be bright yet stylish.

Industry/Entity Type

Life Coaching

```html
<!DOCTYPE html>
<html lang="en">
<head>
<meta charset="utf-8">
<title>Clearpath Coaching – DL Flyer Front</title>
<link rel="stylesheet" href="https://fonts.googleapis.com/css2?family=Raleway:wght@400;500;600;700&display=swap">
<style>
  :root {
    --page-bg: #ece9e4;
    --paper: #ffffff;
    --green: #5db233;
    --green-dark: #3f9a2a;
    --blue: #1c75bc;
    --blue-text: #1a6fb3;
    --sky-top: #2f7fd0;
    --sky-mid: #5fa6e6;
    --sky-light: #cfe6f8;
    --steel: #3b4450;
    --ink: #2b2b2b;
  }
  * { box-sizing: border-box; margin: 0; padding: 0; }
  html, body { width: 1200px; height: 1000px; overflow: hidden; }
  body {
    background: var(--page-bg);
    font-family: "Raleway", Arial, sans-serif;
    color: var(--ink);
    position: relative;
  }
  .brochure {
    position: absolute; left: 69px; top: 47px;
    width: 1062px; height: 819px;
    background: var(--paper);
    box-shadow: 0 6px 18px rgba(0,0,0,.25);
    overflow: hidden;
  }
  .panel { position: absolute; top: 0; height: 819px; }
  .panel--testimonials { left: 0; width: 351px; }
  .panel--intro { left: 351px; width: 353px; }
  .panel--cover { left: 704px; width: 358px; border-left: 1px solid #ddd; }

  /* testimonials */
  .testimonials {
    position: absolute; left: 0; top: 0; width: 351px; height: 577px;
    background: var(--green); color: #fff; padding: 30px 22px 0 28px;
  }
  .testimonials__title { font-size: 16px; font-weight: 700; margin-bottom: 12px; }
  .quote { font-size: 11.7px; line-height: 15px; margin-bottom: 15px; }
  .quote__mark { color: var(--green-dark); font-size: 24px; font-weight: 700; line-height: 0; vertical-align: -7px; }
  .quote__name { display: block; }
  .photo-group {
    position: absolute; left: 0; top: 577px; width: 351px; height: 242px;
    background:
      radial-gradient(ellipse 140px 90px at 20% 35%, rgba(255,244,214,.9), transparent 70%),
      linear-gradient(160deg, #f7dcae 0%, #e6a968 40%, #b9764a 75%, #7d5a43 100%);
  }

  /* intro */
  .offer {
    position: absolute; left: 30px; top: 36px; width: 293px; height: 78px;
    background: var(--blue); border-radius: 8px; color: #fff; text-align: center;
    padding-top: 8px;
  }
  .offer__title { font-size: 17.5px; line-height: 21px; }
  .offer__note { font-size: 13px; line-height: 16px; }
  .photo-coaches {
    position: absolute; left: 44px; top: 148px; width: 266px; height: 175px;
    border-radius: 10px; border: 3px solid #fff;
    box-shadow: 0 0 0 1px #ccc, 0 2px 5px rgba(0,0,0,.2);
    background: linear-gradient(135deg, #6b5d52 0%, #3e3632 45%, #8a8c94 100%);
  }
  .intro-text {
    position: absolute; left: 36px; top: 360px; width: 281px;
    font-size: 14px; line-height: 19.3px; text-align: center;
  }
  .intro-text p + p { margin-top: 18px; }
  .brand {
    position: absolute; left: 0; width: 100%; text-align: center;
    color: var(--blue-text); font-weight: 600;
  }
  .brand__dot {
    display: block; margin: 0 auto 10px; border-radius: 50%;
    background: var(--green);
  }
  .brand--intro { top: 570px; font-size: 19px; line-height: 22px; }
  .brand--intro .brand__dot { width: 92px; height: 92px; }
  .contact { position: absolute; left: 0; width: 100%; text-align: center; }
  .contact--phone { top: 727px; font-size: 23px; display: flex; justify-content: center; align-items: center; gap: 6px; }
  .contact--email { top: 757px; font-size: 13px; font-weight: 500; display: flex; justify-content: center; align-items: center; gap: 6px; }
  .contact--web { top: 777px; font-size: 13px; }
  .contact--web span, .cover-web span { color: var(--green); }

  /* cover */
  .sky {
    position: absolute; left: 0; top: 0; width: 358px; height: 620px;
    background:
      radial-gradient(circle 110px at 95px 0px, rgba(255,255,255,.95), rgba(255,230,210,.35) 60%, transparent 100%),
      radial-gradient(ellipse 170px 160px at 170px 240px, rgba(59,68,80,.85), rgba(59,68,80,.35) 55%, transparent 80%),
      radial-gradient(ellipse 26px 200px at 165px 380px, rgba(120,160,200,.8), transparent 90%),
      radial-gradient(ellipse 90px 70px at 330px 330px, rgba(255,255,255,.85), transparent 75%),
      radial-gradient(ellipse 120px 80px at 320px 470px, rgba(255,255,255,.9), transparent 75%),
      radial-gradient(ellipse 70px 50px at 30px 320px, rgba(255,255,255,.55), transparent 75%),
      linear-gradient(180deg, var(--sky-top) 0%, var(--sky-mid) 45%, var(--sky-light) 85%, #fff 100%);
  }
  .cover-label {
    position: absolute; right: 30px; top: 30px; color: #fff;
    font-size: 11px; font-weight: 700;
  }
  .swoosh { position: absolute; left: 0; top: 440px; }
  .circle-photo {
    position: absolute; border-radius: 50%; border: 4px solid #fff;
    box-shadow: 0 1px 4px rgba(0,0,0,.2); overflow: hidden;
  }
  .circle-photo--meditation { left: 14px; top: 400px; width: 164px; height: 164px;
    background: linear-gradient(180deg, #bcd9ef 0%, #e9eef2 45%, #b7b4d4 62%, #7e9a5a 80%, #5b7f3a 100%); }
  .circle-photo--yoga { left: 186px; top: 465px; width: 146px; height: 146px;
    background: linear-gradient(180deg, #b8d4ec 0%, #e7eff5 55%, #d9d2c4 100%); }
  .circle-photo__label {
    position: absolute; left: 0; width: 100%; bottom: 14px; text-align: center;
    font-size: 10.5px; font-weight: 700; color: #111;
  }
  .brand--cover { top: 620px; font-size: 21px; line-height: 24px; }
  .brand--cover .brand__dot { width: 96px; height: 96px; margin-bottom: 14px; }
  .cover-web { position: absolute; left: 0; width: 100%; top: 780px; text-align: center; font-size: 12.5px; }
</style>
</head>
<body>
<main class="brochure">

  <section class="panel panel--testimonials">
    <div class="testimonials">
      <h2 class="testimonials__title">Happy Clients Testimonials</h2>
      <p class="quote"><span class="quote__mark">“</span>I have lost 10 kilos and now have the energy to play with my kids. Thanks Mara for you support/guidance and helping me get rid of my limiting beliefs. I feel I can achieve anything now! The sky’s the limit <span class="quote__mark">”</span><span class="quote__name">Jodie, Mosman</span></p>
      <p class="quote"><span class="quote__mark">“</span>I had always wanted to start up own café however every time it came to putting it into practice I would procrastinate and not achieve anything. I became overwhelmed with the whole process and never achieved anything. Mara put it into bite sized chunks and helped me to set small achievable goals. I am now a happy café owner.<span class="quote__mark">”</span><span class="quote__name">Tessa, Double Bay</span></p>
      <p class="quote"><span class="quote__mark">“</span>Mara has helped to change my life around in all aspects. I would have been lost without her. Thanks Mara for your professionalism, support and guidance.<span class="quote__mark">”</span><span class="quote__name">Carla, Cremorne</span></p>
      <p class="quote"><span class="quote__mark">“</span>I was so busy with kids, work, and my husband I lost who I was. Mara has helped me find the person I am again.<span class="quote__mark">”</span><span class="quote__name">Leah, Chatswood</span></p>
      <p class="quote"><span class="quote__mark">“</span>When I started with Coach Mara, I didn’t know anything about coaching. I called her because she helped a friend of mine make a career change that was a perfect fit for her. I had the opportunity to make a change too and did not know where to start. I am now in a job that I love. I would recommend Mara to everyone.<span class="quote__mark">”</span><span class="quote__name">Owen, Texas America</span></p>
    </div>
    <div class="photo-group" role="img" aria-label="Photo of a group of happy friends cheering by a coastal road at sunset"></div>
  </section>

  <section class="panel panel--intro">
    <div class="offer">
      <p class="offer__title">Free Introductory Life Coaching<br>Phone/Video session - 20 mins</p>
      <p class="offer__note">(To see if coaching is right for you)</p>
    </div>
    <div class="photo-coaches" role="img" aria-label="Portrait photo of the two coaches"></div>
    <div class="intro-text">
      <p>Clearpath Coaching and Meditation Studio is a professional service that can help you achieve the goals that you are looking for in Life Coaching, Meditation, and Yoga/Pilates.</p>
      <p>If you are ready to take your life to the next level and would like to know more, please contact us.</p>
    </div>
    <div class="brand brand--intro">
      <span class="brand__dot"></span>
      Clearpath Coaching<br>and Meditation Studio
    </div>
    <p class="contact contact--phone">
      <svg width="18" height="18" viewBox="0 0 24 24" aria-hidden="true"><circle cx="12" cy="12" r="10.5" fill="none" stroke="#1c75bc" stroke-width="1.6"/><path d="M8.5 7c.6-.4 1.2-.2 1.5.4l.8 1.6c.2.5.1 1-.3 1.3l-.6.5c.6 1.3 1.6 2.3 2.9 2.9l.5-.6c.3-.4.8-.5 1.3-.3l1.6.8c.6.3.8.9.4 1.5-.7 1.1-1.9 1.5-3.1 1-2.8-1.1-4.9-3.2-6-6-.5-1.2-.1-2.4 1-3.1z" fill="#1c75bc"/></svg>
      02 9000 4127
    </p>
    <p class="contact contact--email">
      <svg width="14" height="10" viewBox="0 0 14 10" aria-hidden="true"><rect x=".6" y=".6" width="12.8" height="8.8" fill="none" stroke="#1c75bc" stroke-width="1.2"/><path d="M.8 1 7 6l6.2-5" fill="none" stroke="#1c75bc" stroke-width="1.2"/></svg>
      hello@clearpathcoaching.com.au
    </p>
    <p class="contact contact--web">www.<span>clearpathcoaching</span>.com.au</p>
  </section>

  <section class="panel panel--cover">
    <div class="sky" role="img" aria-label="Photo of a street signpost against a bright blue cloudy sky with arrows pointing to life, balance, family, career, health and friends"></div>
    <p class="cover-label">LIFE COACHING</p>
    <svg class="swoosh" width="358" height="260" viewBox="0 0 358 260" aria-hidden="true">
      <path d="M0 160 C120 120 250 110 358 135 L358 150 C250 130 120 145 0 190 Z" fill="#1c9ad6"/>
      <path d="M0 180 C120 150 250 150 358 165 L358 180 C250 172 120 180 0 215 Z" fill="var(--green)"/>
      <path d="M0 195 C120 170 250 172 358 182 L358 260 L0 260 Z" fill="#fff"/>
    </svg>
    <div class="circle-photo circle-photo--meditation" role="img" aria-label="Photo of three women meditating outdoors on grass">
      <span class="circle-photo__label">MEDITATION</span>
    </div>
    <div class="circle-photo circle-photo--yoga" role="img" aria-label="Photo of two people in a yoga pose on a beach">
      <span class="circle-photo__label">YOGA/PILATES</span>
    </div>
    <div class="brand brand--cover">
      <span class="brand__dot"></span>
      Clearpath Coaching<br>and Meditation Studio
    </div>
    <p class="cover-web">www.<span>clearpathcoaching</span>.com.au</p>
  </section>

</main>
</body>
</html>
```